We need a designer to help us represent our unique approach to creating lesson plans for digital learning. At the Coastal Workshop for Media Fluency, held in Providence RI this July 13 - 18, we'll use your design with 100 teachers and then put it online to reach hundreds of thousands more.

We have a draft visual of our model that we like - but it's not pretty (Since we are not designers, it looks a little clunky).

Please create a simple and attractive design in two versions: (1) one that we can use as a 1-page printed handout and (2) one that we can use where teachers can fill in sections and write ideas under each section of the graphic.

Why you should bid on this job? We're a leading provider of digital and media literacy curriculum resources with a huge international and national audience. Working with us will establish your expertise in the area of educational multimedia design.

Target Market(s)

Elementary and secondary teachers in public schools

Industry/Entity Type

Digital

Font styles to use
Sans Serif

Requirements
Must have
• TITLE : Digital Literacy Curriculum Framework

1 page version - suitable for use as a poster or 1-page flyer

Fillable form version - suitable for use as a handout with spaces for teachers to write

```html
<!DOCTYPE html>
<html lang="en">
<head>
<meta charset="UTF-8">
<title>Digital Literacy Curriculum Framework</title>
<link rel="stylesheet" href="https://fonts.googleapis.com/css2?family=Open+Sans:wght@400;600;700&display=swap">
<style>
  :root {
    --paper: #f2f0d3;
    --ring: #e1dfb1;
    --ink: #7a6850;
    --divider: #ffffff;
    --self: #fdca98;
    --learners: #f9a54a;
    --community: #a8c1b3;
    --context: #fcd461;
    --subject: #43a5b3;
  }
  html, body {
    margin: 0;
    padding: 0;
    width: 848px;
    height: 1200px;
    overflow: hidden;
    background: var(--paper);
  }
  .framework {
    display: block;
    width: 848px;
    height: 1200px;
    font-family: "Open Sans", sans-serif;
  }
  .title {
    fill: var(--ink);
    font-size: 27px;
    font-weight: 700;
    letter-spacing: 1.2px;
  }
  .corner-label {
    fill: var(--ink);
    font-size: 20px;
    letter-spacing: 0.5px;
  }
  .ring-label {
    fill: var(--ink);
    font-size: 18px;
    letter-spacing: 1px;
  }
  .quadrant-label {
    fill: #ffffff;
    font-size: 20px;
  }
  .subject-label {
    fill: #ffffff;
    font-size: 21px;
  }
  .axis { stroke: var(--ink); stroke-width: 1.4; }
  .outer-ring { fill: var(--ring); stroke: var(--ink); stroke-width: 2; }
  .segment-divider { stroke: var(--divider); stroke-width: 1.6; }
  .quadrant-divider { stroke: var(--divider); stroke-width: 1.2; }
  .subject-ring { fill: none; stroke: var(--ink); stroke-width: 1.4; }
</style>
</head>
<body>
<svg class="framework" viewBox="0 0 848 1200" xmlns="http://www.w3.org/2000/svg" aria-label="Digital Literacy Curriculum Framework diagram">
  <defs>
    <path id="label-track" d="M203.2,359.7 A345,345 0 1 1 646.8,888.3 A345,345 0 1 1 203.2,359.7"/>
  </defs>

  <rect width="848" height="1200" fill="var(--paper)"/>

  <text class="title" x="442" y="80" text-anchor="middle">DIGITAL LITERACY CURRICULUM FRAMEWORK</text>

  <!-- quadrant axes -->
  <line class="axis" x1="425" y1="128" x2="425" y2="218"/>
  <line class="axis" x1="425" y1="1030" x2="425" y2="1200"/>
  <line class="axis" x1="0" y1="624" x2="19" y2="624"/>
  <line class="axis" x1="831" y1="624" x2="848" y2="624"/>

  <text class="corner-label" x="140" y="151" text-anchor="middle">PURPOSE</text>
  <text class="corner-label" x="738" y="158" text-anchor="middle">ASSESMENT</text>
  <text class="corner-label" x="138" y="1147" text-anchor="middle">CONTENT</text>
  <text class="corner-label" x="727" y="1154" text-anchor="middle">PEDAGOGY</text>

  <!-- outer ring of planning elements -->
  <circle class="outer-ring" cx="425" cy="624" r="406"/>
  <line class="segment-divider" x1="296.8" y1="447.6" x2="186.3" y2="295.5"/>
  <line class="segment-divider" x1="557.8" y1="451.1" x2="672.2" y2="302.0"/>
  <line class="segment-divider" x1="636.9" y1="674.8" x2="819.6" y2="718.6"/>
  <line class="segment-divider" x1="425" y1="842" x2="425" y2="1029"/>
  <line class="segment-divider" x1="214.0" y1="678.9" x2="32.0" y2="726.3"/>

  <text class="ring-label"><textPath href="#label-track" startOffset="247" text-anchor="middle">STANDARDS</textPath></text>
  <text class="ring-label"><textPath href="#label-track" startOffset="665" text-anchor="middle">WORK PRODUCTS</textPath></text>
  <text class="ring-label"><textPath href="#label-track" startOffset="1094" text-anchor="middle">INSTRUCTIONAL STRATEGIES</textPath></text>
  <text class="ring-label"><textPath href="#label-track" startOffset="1552" text-anchor="middle">TOOLS</textPath></text>
  <text class="ring-label"><textPath href="#label-track" startOffset="1983" text-anchor="middle">TEXT</textPath></text>

  <!-- inner quadrants -->
  <path d="M425,624 L207,624 A218,218 0 0 1 425,406 Z" fill="var(--self)"/>
  <path d="M425,624 L425,406 A218,218 0 0 1 643,624 Z" fill="var(--learners)"/>
  <path d="M425,624 L643,624 A218,218 0 0 1 425,842 Z" fill="var(--community)"/>
  <path d="M425,624 L425,842 A218,218 0 0 1 207,624 Z" fill="var(--context)"/>
  <line class="quadrant-divider" x1="425" y1="406" x2="425" y2="842"/>
  <line class="quadrant-divider" x1="207" y1="624" x2="643" y2="624"/>

  <text class="quadrant-label" text-anchor="middle" transform="translate(296,492) rotate(-45)">Self</text>
  <text class="quadrant-label" text-anchor="middle" transform="translate(558,492) rotate(45)">Learners</text>
  <text class="quadrant-label" text-anchor="middle" transform="translate(550,752) rotate(125)">Community</text>
  <text class="quadrant-label" text-anchor="middle" transform="translate(296,752) rotate(225)">Context</text>

  <!-- subject core -->
  <circle class="subject-ring" cx="425" cy="624" r="91"/>
  <circle cx="430" cy="628" r="81" fill="var(--subject)"/>
  <text class="subject-label" x="425" y="632" text-anchor="middle">SUBJECT</text>
</svg>
</body>
</html>
```